Homemaking training schools needs a Business Card design

Designer, Hello!

No special requirements, good-looking enough.
--------------------------------------------------------------------------

Name: Marcus Dole
Chairman
Tel: 0574-71948263
Mobile: 13857420916
Email: kelvora@mailnest.example
Web: www.prt2019.example
Add: No.258, LanpingJie, BeiyuanQu, Ningbo, Zhejiang

LOGO
Ningbo PRT Homemaking Training School

Target Market(s)

pregnant women, mothers, infants, the elderly and families, including cleaning, cooking, nursing training.

Industry/Entity Type

Business

Contact Information for Business Card

Name: Marcus Dole
Chairman
Tel: 0574-71948263
Mobile: 13857420916
Email: kelvora@mailnest.example
Web: www.prt2019.example

LOGO

Font styles to use
Serif
Sans Serif
Decorative

Requirements
Nice to have
• Feels: clean, specifications, safety, comfort, warmth and happiness.

```html
<!DOCTYPE html>
<html lang="en">
<head>
<meta charset="UTF-8">
<title>PingRuiTang Business Card</title>
<link href="https://fonts.googleapis.com/css2?family=Roboto:wght@400;500;700&display=swap" rel="stylesheet">
<style>
  :root {
    --magenta: #ec1c8f;
    --blue: #1e7fc6;
    --white: #ffffff;
    --stage: #e9e6e1;
  }
  * { box-sizing: border-box; margin: 0; padding: 0; }
  html, body { width: 1200px; height: 950px; overflow: hidden; }
  body { background: var(--stage); position: relative; font-family: "Roboto", Arial, sans-serif; }

  .card {
    position: absolute; width: 620px; height: 354px;
    border-radius: 4px; overflow: hidden;
    box-shadow: 0 10px 28px rgba(0,0,0,.22);
  }

  /* Shared name block */
  .brand { display: flex; align-items: center; gap: 12px; }
  .brand-dot { width: 20px; height: 20px; border-radius: 50%; flex: none; }
  .brand-name { font-family: "Roboto", Arial, sans-serif; font-weight: 700; line-height: 1; }

  /* Front */
  .card-front { left: 100px; top: 80px; background: var(--magenta); color: var(--white); }
  .front-brand { position: absolute; left: 0; right: 0; top: 112px; justify-content: center; }
  .front-brand .brand-dot { background: var(--white); }
  .front-brand .brand-name { font-size: 48px; color: var(--white); }
  .front-web {
    position: absolute; left: 0; right: 0; top: 252px; text-align: center;
    font-size: 15px; letter-spacing: 6px; font-weight: 500;
  }

  /* Back */
  .card-back { left: 480px; top: 500px; background: var(--white); }
  .back-wave { position: absolute; inset: 0; }
  .back-brand { position: absolute; left: 60px; top: 80px; }
  .back-brand .brand-dot { width: 16px; height: 16px; background: var(--magenta); }
  .back-brand .brand-name { font-size: 38px; color: var(--blue); }

  .holder { position: absolute; left: 205px; top: 222px; color: var(--white); text-align: center; }
  .holder-name { font-weight: 700; font-size: 21px; }
  .holder-role { font-size: 14px; margin-top: 3px; padding-top: 3px; border-top: 1px solid rgba(255,255,255,.6); }

  .address {
    position: absolute; right: 24px; top: 152px; text-align: right; font-style: normal;
    color: var(--white); font-size: 14px; line-height: 1.5;
  }

  .contacts { position: absolute; left: 22px; top: 268px; color: var(--white); font-size: 15px; list-style: none; }
  .contacts li { display: flex; align-items: center; gap: 8px; line-height: 24px; }
  .contacts svg { width: 15px; height: 15px; fill: var(--white); flex: none; }
</style>
</head>
<body>

<section class="card card-front">
  <div class="brand front-brand">
    <span class="brand-dot"></span>
    <span class="brand-name">PingRuiTang</span>
  </div>
  <p class="front-web">www.prt2019.example</p>
</section>

<section class="card card-back">
  <svg class="back-wave" viewBox="0 0 620 354" preserveAspectRatio="none">
    <path d="M0,222 Q330,200 620,100 L620,354 L0,354 Z" fill="var(--blue)"/>
    <path d="M0,216 Q330,194 620,94" fill="none" stroke="var(--magenta)" stroke-width="4"/>
  </svg>

  <div class="brand back-brand">
    <span class="brand-dot"></span>
    <span class="brand-name">PingRuiTang</span>
  </div>

  <div class="holder">
    <p class="holder-name">Marcus Dole</p>
    <p class="holder-role">Chairman</p>
  </div>

  <address class="address">
    No.258, LanpingJie,<br>
    BeiyuanQu, Ningbo, Zhejiang<br>
    www.prt2019.example
  </address>

  <ul class="contacts">
    <li>
      <svg viewBox="0 0 24 24"><path d="M6.6 10.8a15 15 0 0 0 6.6 6.6l2.2-2.2a1 1 0 0 1 1-.25 11.4 11.4 0 0 0 3.6.57 1 1 0 0 1 1 1V20a1 1 0 0 1-1 1A17 17 0 0 1 3 4a1 1 0 0 1 1-1h3.5a1 1 0 0 1 1 1c0 1.25.2 2.45.57 3.57a1 1 0 0 1-.25 1z"/></svg>
      0574-71948263
    </li>
    <li>
      <svg viewBox="0 0 24 24"><path d="M7 1h10a2 2 0 0 1 2 2v18a2 2 0 0 1-2 2H7a2 2 0 0 1-2-2V3a2 2 0 0 1 2-2zm0 3v14h10V4zm5 15.5a1 1 0 1 0 0 2 1 1 0 0 0 0-2z"/></svg>
      13857420916
    </li>
    <li>
      <svg viewBox="0 0 24 24"><path d="M2 5h20v14H2zm2 2v.5l8 5 8-5V7zm0 2.8V17h16V9.8l-8 5z"/></svg>
      kelvora@mailnest.example
    </li>
  </ul>
</section>

</body>
</html>
```